Networking Events Calendar/Diary

We need a responsive website that can act as both an online diary/calendar and a resource for community and networking events similar to brimtolvenquarrix.com (we do not want a clone, but one with similar functionality). We need to be able to host adverts, have a client area for clients to add their own events to the diary. This needs to have the functionality that clients have to pay to add recurring events. Some integration would be useful so that if a clients already has their own online diary on their website then using an API possibly to also add that event into our online diary

Industry/Entity Type

Events

Coding

Coded - Design and coding required

Number of Pages Required

5+ page

Requirements
Must have
• My project must have a calendar area, space for ads, be responsive and easily viewable on mobile. A subscribers area for clients and a way to purchase premium status so that premium events are highlighted.

```html
<!DOCTYPE html>
<html lang="en">
<head>
<meta charset="utf-8">
<title>Velmora Events</title>
<link href="https://fonts.googleapis.com/css2?family=Roboto:wght@400;500;700&display=swap" rel="stylesheet">
<style>
:root{
  --green:#5a9e12;--green-dark:#4a8a0c;--orange:#f07c16;--dark:#2b2b2b;--darker:#232323;
  --text:#333;--muted:#666;--panel:#efefef;--line:#ddd;--white:#fff;--black:#111;
}
*{box-sizing:border-box;margin:0;padding:0}
html,body{width:1200px;height:2217px;overflow:hidden}
body{font-family:'Roboto',Arial,sans-serif;color:var(--text);background:var(--white);position:relative}
.abs{position:absolute}
a{color:inherit;text-decoration:none}
.topbar{left:0;top:0;width:1200px;height:52px;background:#efefef}
.sq{display:inline-block;width:17px;height:17px;background:#555;border-radius:3px;margin-right:14px}
.toplinks{left:592px;top:18px;font-size:13px;color:#444}
.toplinks span{margin:0 6px;color:#999}
.btn-login{left:868px;top:10px;width:100px;height:32px;background:var(--black);color:#fff;font-size:12px;font-weight:500;display:flex;align-items:center;justify-content:center;gap:6px}
.btn-register{left:972px;top:10px;width:100px;height:32px;background:var(--orange);color:#fff;font-size:12px;font-weight:500;display:flex;align-items:center;justify-content:center;gap:6px}
.btn-search{left:1084px;top:10px;width:41px;height:32px;background:#fff;border:1px solid #ccc;display:flex;align-items:center;justify-content:center}
.logo{left:77px;top:88px;font-size:40px;font-weight:500;color:var(--text)}
.logo b{color:var(--green);font-weight:500}
.banner-ad{left:454px;top:70px;width:672px;height:84px;background:linear-gradient(90deg,#9a2418,#7a1612 60%,#4e1410)}
.nav{left:0;top:176px;width:1200px;height:50px;background:linear-gradient(#6ab21a,var(--green-dark));display:flex;padding-left:68px}
.nav a{color:#fff;font-size:12px;font-weight:500;line-height:50px;padding:0 14px;border-right:1px solid rgba(0,0,0,.15)}
.nav a:last-child{border:0}
.welcome{left:75px;top:242px;width:330px;height:355px;background:var(--panel);border:2px solid #ddd;padding:20px 16px}
.welcome h2{font-size:22px;font-weight:500;color:var(--green);line-height:26px}
.welcome h2 span{display:block;color:var(--text)}
.welcome p{font-size:13.4px;line-height:26px;color:#555;margin-top:8px}
.btn-black{background:linear-gradient(#333,#000);color:#fff;font-size:14px;font-weight:500;display:inline-flex;align-items:center;justify-content:center}
.welcome .btn-black{width:135px;height:34px;margin-top:18px}
.slider{left:436px;top:242px;width:690px;height:354px;border:2px solid #ddd}
.slider .photo{width:100%;height:100%;background:linear-gradient(120deg,#e7eaee,#b5bcc6 45%,#5b6474)}
.slider .caption{position:absolute;left:0;bottom:0;width:100%;height:76px;background:rgba(40,40,40,.85);padding:12px 20px;color:#fff}
.slider .caption h4{font-size:22px;font-weight:500}
.slider .caption p{font-size:13px;color:var(--orange);margin-top:8px;font-weight:500}
.arrow{position:absolute;top:160px;width:34px;height:34px;border-radius:50%;background:#333;opacity:.85;display:flex;align-items:center;justify-content:center}
.sec-head{height:50px;display:flex;align-items:center;border-top:5px solid var(--green)}
.sec-head .tab{width:60px;height:50px;background:var(--green);margin-top:-5px;display:flex;align-items:center;justify-content:center;clip-path:polygon(0 0,100% 0,100% 75%,50% 100%,0 75%)}
.sec-head h3{font-size:18px;font-weight:500;margin-left:28px;text-transform:uppercase}
.events{left:75px;top:632px;width:603px}
.events .grid{display:grid;grid-template-columns:1fr 1fr;margin-top:10px}
.event{padding:10px 0 22px 0}
.event:nth-child(2n){padding-left:24px;border-left:1px solid var(--line)}
.event:nth-child(-n+2){border-bottom:1px solid var(--line)}
.event:nth-child(n+3){padding-top:18px}
.event h4{font-size:20.5px;line-height:27px;color:var(--orange);font-weight:500}
.meta{font-size:13px;color:var(--green);font-weight:500;margin-top:10px;display:flex;align-items:center;gap:8px}
.event .social{margin-top:12px}
.event .sq{width:13px;height:13px;margin-right:14px}
.event .btn-black{width:105px;height:34px;margin-top:14px;font-size:14px}
.tips{left:705px;top:632px;width:421px}
.tip{height:126px;background:var(--panel);margin-top:14px;display:flex;align-items:center;padding:0 20px}
.tip:first-of-type{margin-top:16px}
.thumb{flex:none}
.tip .thumb{width:120px;height:98px}
.tip p{font-size:14px;line-height:25px;color:#555;margin-left:20px}
.divider{left:75px;top:1138px;width:1051px;height:1px;background:var(--line)}
.blog{left:75px;top:1170px;width:691px}
.post{height:196px;margin-top:20px;background:linear-gradient(90deg,#e8e8e8,#f7f7f7);display:flex;padding:25px 24px}
.post:first-of-type{margin-top:17px}
.post .thumb{width:204px;height:146px}
.post .body{margin-left:24px}
.post h4{font-size:21px;color:var(--orange);font-weight:500}
.post .meta{margin-top:12px}
.post p{font-size:14px;line-height:24px;color:#555;margin-top:8px}
.readmore{font-size:14px;font-weight:500;color:#222;margin-top:12px;display:block}
.side-ad{left:825px;top:1170px;width:277px;height:230px;background:linear-gradient(#f4f4f4,#d8d8d8)}
.news{left:795px;top:1452px;width:331px}
.news-item{padding:14px 0 12px;border-bottom:1px solid var(--line)}
.news-item:last-child{border:0}
.news-item p{font-size:14px;line-height:24px;color:#555;margin-top:6px}
.news-item .readmore{margin-top:6px}
.footer{left:0;top:1900px;width:1200px;height:258px;background:var(--dark);padding:34px 75px;display:flex}
.footer h5{font-size:14px;color:var(--green);font-weight:500;text-transform:uppercase}
.footer ul{list-style:none}
.footer li{font-size:13px;color:#ddd;line-height:20px;margin-bottom:10px}
.fcols{display:flex;margin-top:14px}
.fcol1{width:237px}.fcol2{width:271px}.fcol3{width:210px}
.subscribe input{width:333px;height:41px;border:0;padding:0 16px;font-size:15px;font-family:inherit;margin-top:16px;color:#777}
.subscribe .btn{float:right;margin-top:12px;background:var(--orange);color:#fff;font-size:16px;font-weight:500;width:106px;height:34px;display:flex;align-items:center;justify-content:center}
.subscribe .connect{clear:both;padding-top:18px}
.subscribe .social{margin-top:14px}
.subscribe .sq{width:21px;height:21px;background:#ddd;margin-right:20px}
.bottom{left:0;top:2158px;width:1200px;height:59px;background:var(--darker);font-size:12px;color:#999;display:flex;align-items:center;justify-content:space-between;padding:0 75px}
.bottom span i{margin:0 10px;font-style:normal}
</style>
</head>
<body>

<div class="abs topbar"></div>
<div class="abs social" style="left:75px;top:17px"><span class="sq"></span><span class="sq"></span><span class="sq"></span><span class="sq"></span></div>
<div class="abs toplinks">Contact Us<span>|</span>Tell a Friend<span>|</span>Useful Links</div>
<a class="abs btn-login"><svg width="10" height="12" viewBox="0 0 10 12"><rect x="0" y="5" width="10" height="7" fill="#fff"/><path d="M2 5V3a3 3 0 0 1 6 0v2" stroke="#fff" stroke-width="1.5" fill="none"/></svg>LOG IN</a>
<a class="abs btn-register"><svg width="10" height="12" viewBox="0 0 10 12"><circle cx="5" cy="3" r="3" fill="#fff"/><path d="M0 12a5 5 0 0 1 10 0z" fill="#fff"/></svg>REGISTER</a>
<a class="abs btn-search"><svg width="14" height="14" viewBox="0 0 14 14"><circle cx="6" cy="6" r="4.5" stroke="#5a9e12" stroke-width="2" fill="none"/><path d="M9.5 9.5 13 13" stroke="#5a9e12" stroke-width="2"/></svg></a>

<div class="abs logo"><b>Velmora</b> Events</div>
<div class="abs banner-ad" role="img" aria-label="Advertising banner space"></div>

<nav class="abs nav">
  <a>HOME</a><a>EVENTS BY REGION</a><a>EVENTS BY TOWN/CITY</a><a>EVENTS FOR WOMEN</a><a>WORKSHOPS/SEMINARS</a><a>BUSINESS SHOWS</a><a>BLOG</a><a>EVENT FRANCHISES</a>
</nav>

<section class="abs welcome">
  <h2>WELCOME<span>TO VELMORA EVENTS</span></h2>
  <p>Aliquam molestie, mi et imperdiet euismod, dui purus auctor tellus, et interdum lacus lectus et ante. Sed accumsan sollicitudin sapien, sit amet adipiscing turpis gravida ac. In congue, neque ac lobortis volutpat, libero mauris varius mi, vitae suscipit ipsum ligula vitae risus. Duis aliquam nibh a dui iaculis viverra id a velit.</p>
  <a class="btn-black">READ MORE</a>
</section>

<section class="abs slider">
  <div class="photo" role="img" aria-label="Business people networking at an event"></div>
  <span class="arrow" style="left:8px"><svg width="12" height="14"><path d="M9 1 3 7l6 6" stroke="#fff" stroke-width="2.5" fill="none"/></svg></span>
  <span class="arrow" style="right:8px"><svg width="12" height="14"><path d="m3 1 6 6-6 6" stroke="#fff" stroke-width="2.5" fill="none"/></svg></span>
  <div class="caption"><h4>Lorem ipsum dolor sit amet egestas risus in magna..</h4><p>◷ &nbsp;6pm - 9pm &nbsp;| &nbsp;⚲ &nbsp;Calder Lane,Dunmore</p></div>
</section>

<section class="abs events">
  <div class="sec-head"><span class="tab"><svg width="22" height="22" viewBox="0 0 22 22"><rect x="1" y="3" width="20" height="18" fill="none" stroke="#fff" stroke-width="2"/><path d="M1 8h20M6 1v4M16 1v4M5 12h3M10 12h3M15 12h3M5 16h3M10 16h3" stroke="#fff" stroke-width="2"/></svg></span><h3>Upcoming Events</h3></div>
  <div class="grid">
    <div class="event"><h4>Lorem ipsum dolor sit amet egestas risus in magna..</h4><div class="meta">◷ &nbsp;6pm - 9pm</div><div class="meta">⚲ &nbsp;Calder Lane,Dunmore</div><div class="social"><span class="sq"></span><span class="sq"></span><span class="sq"></span><span class="sq"></span></div><a class="btn-black">More Info</a></div>
    <div class="event"><h4>Lorem ipsum dolor sit amet egestas risus in magna..</h4><div class="meta">◷ &nbsp;6pm - 9pm</div><div class="meta">⚲ &nbsp;Calder Lane,Dunmore</div><div class="social"><span class="sq"></span><span class="sq"></span><span class="sq"></span><span class="sq"></span></div><a class="btn-black">More Info</a></div>
    <div class="event"><h4>Lorem ipsum dolor sit amet egestas risus in magna..</h4><div class="meta">◷ &nbsp;6pm - 9pm</div><div class="meta">⚲ &nbsp;Calder Lane,Dunmore</div><div class="social"><span class="sq"></span><span class="sq"></span><span class="sq"></span><span class="sq"></span></div><a class="btn-black">More Info</a></div>
    <div class="event"><h4>Lorem ipsum dolor sit amet egestas risus in magna..</h4><div class="meta">◷ &nbsp;6pm - 9pm</div><div class="meta">⚲ &nbsp;Calder Lane,Dunmore</div><div class="social"><span class="sq"></span><span class="sq"></span><span class="sq"></span><span class="sq"></span></div><a class="btn-black">More Info</a></div>
  </div>
</section>

<section class="abs tips">
  <div class="sec-head"><span class="tab"><svg width="22" height="20" viewBox="0 0 22 20"><rect x="8" y="1" width="6" height="5" fill="#fff"/><rect x="1" y="14" width="6" height="5" fill="#fff"/><rect x="15" y="14" width="6" height="5" fill="#fff"/><rect x="8" y="14" width="6" height="5" fill="#fff"/><path d="M11 6v8M4 14v-4h14v4" stroke="#fff" stroke-width="2" fill="none"/></svg></span><h3>Networking Tips</h3></div>
  <div class="tip"><div class="thumb" role="img" aria-label="Network cables" style="background:linear-gradient(135deg,#c9b24a,#46505c)"></div><p>Duis aliquam nibh a dui iaculis viverra id a velit. Vivamus egestas risus in magna varius commodo.</p></div>
  <div class="tip"><div class="thumb" role="img" aria-label="Hands holding a tablet" style="background:linear-gradient(135deg,#2a4a7a,#1a1e2a)"></div><p>Duis aliquam nibh a dui iaculis viverra id a velit. Vivamus egestas risus in magna varius commodo.</p></div>
  <div class="tip"><div class="thumb" role="img" aria-label="Social network diagram" style="background:linear-gradient(135deg,#1a1a1a,#3a3a3a)"></div><p>Duis aliquam nibh a dui iaculis viverra id a velit. Vivamus egestas risus in magna varius commodo.</p></div>
</section>

<div class="abs divider"></div>

<section class="abs blog">
  <div class="sec-head"><span class="tab"><svg width="18" height="18" viewBox="0 0 18 18"><circle cx="3" cy="15" r="2.5" fill="#fff"/><path d="M1 7a10 10 0 0 1 10 10M1 1a16 16 0 0 1 16 16" stroke="#fff" stroke-width="2.5" fill="none"/></svg></span><h3>Latest Blog Posts</h3></div>
  <article class="post"><div class="thumb" role="img" aria-label="Speaker in front of a world map screen" style="background:linear-gradient(135deg,#2a6fd0,#0a2a6a)"></div><div class="body"><h4>Lorem ipsum dolor sit amet egestas..</h4><div class="meta">▦ &nbsp;Dec11, 2015 &nbsp;| &nbsp;● &nbsp;By Admin</div><p>Duis aliquam nibh a dui iaculis viverra id a velit. Vivamus egestas risus in magna varius commodo..</p><a class="readmore">Read More »</a></div></article>
  <article class="post"><div class="thumb" role="img" aria-label="Exhibition hall with stands" style="background:linear-gradient(135deg,#c8c0b0,#7a8a9a)"></div><div class="body"><h4>Lorem ipsum dolor sit amet egestas..</h4><div class="meta">▦ &nbsp;Dec11, 2015 &nbsp;| &nbsp;● &nbsp;By Admin</div><p>Duis aliquam nibh a dui iaculis viverra id a velit. Vivamus egestas risus in magna varius commodo..</p><a class="readmore">Read More »</a></div></article>
  <article class="post"><div class="thumb" role="img" aria-label="Audience at a seminar" style="background:linear-gradient(135deg,#d8d4cc,#6a5a4a)"></div><div class="body"><h4>Lorem ipsum dolor sit amet egestas..</h4><div class="meta">▦ &nbsp;Dec11, 2015 &nbsp;| &nbsp;● &nbsp;By Admin</div><p>Duis aliquam nibh a dui iaculis viverra id a velit. Vivamus egestas risus in magna varius commodo..</p><a class="readmore">Read More »</a></div></article>
</section>

<aside class="abs side-ad" role="img" aria-label="Sidebar advertising space"></aside>

<section class="abs news">
  <div class="sec-head"><span class="tab"><svg width="22" height="20" viewBox="0 0 22 20"><rect x="8" y="1" width="6" height="5" fill="#fff"/><rect x="1" y="14" width="6" height="5" fill="#fff"/><rect x="15" y="14" width="6" height="5" fill="#fff"/><rect x="8" y="14" width="6" height="5" fill="#fff"/><path d="M11 6v8M4 14v-4h14v4" stroke="#fff" stroke-width="2" fill="none"/></svg></span><h3>Networking News</h3></div>
  <div class="news-item"><div class="meta">▦ &nbsp;Dec11, 2015 &nbsp;| &nbsp;● &nbsp;By Admin</div><p>Duis aliquam nibh a dui iaculis viverra id a velit. Vivamus egestas risus in magna varius...</p><a class="readmore">Read More »</a></div>
  <div class="news-item"><div class="meta">▦ &nbsp;Dec11, 2015 &nbsp;| &nbsp;● &nbsp;By Admin</div><p>Duis aliquam nibh a dui iaculis viverra id a velit. Vivamus egestas risus in magna varius...</p><a class="readmore">Read More »</a></div>
  <div class="news-item"><div class="meta">▦ &nbsp;Dec11, 2015 &nbsp;| &nbsp;● &nbsp;By Admin</div><p>Duis aliquam nibh a dui iaculis viverra id a velit. Vivamus egestas risus in magna varius...</p><a class="readmore">Read More »</a></div>
</section>

<footer class="abs footer">
  <div style="width:719px">
    <h5>More Info About Velmora Events</h5>
    <div class="fcols">
      <ul class="fcol1"><li>Login</li><li>Contact Us</li><li>Subscribe to our Weekly Bulletin</li><li>Register to Add Events</li><li>Testimonials</li></ul>
      <ul class="fcol2"><li>Online Marketing Mentoring Sessions</li><li>Download 'A Quick Guide to Business Networking'</li><li>Networking Events by Region</li><li>Networking Events by Town/City</li><li>Networking Events for Women</li></ul>
      <ul class="fcol3"><li>Workshops/Seminars</li><li>Business Shows</li><li>Blog</li><li>Networking News</li><li>Support</li><li>Run Your Own Events</li></ul>
    </div>
  </div>
  <div class="subscribe" style="width:333px">
    <h5>Subscribe Newsletter</h5>
    <input type="text" value="Email Address" aria-label="Email Address">
    <a class="btn">Subscribe</a>
    <h5 class="connect">Connect Us</h5>
    <div class="social"><span class="sq"></span><span class="sq"></span><span class="sq"></span><span class="sq"></span></div>
  </div>
</footer>

<div class="abs bottom"><span>Copyright © 2015 Velmora Events.All Right Reserved</span><span>Terms &amp; Conditions<i>|</i>Privacy Statement</span></div>

</body>
</html>
```